Larkfield Ridge Management

I need a professional website. My current website is larkfieldridgemanagement.com and I hate it. It was created with some AI tool very quickly because I needed a site up and running with no advanced notice. I’m open to all designs .. I trust you, the professionals will deliver the results I’m anxiously awaiting! :)

```html
<!DOCTYPE html>
<html lang="en">
<head>
<meta charset="utf-8">
<title>Larkfield Ridge Management</title>
<link rel="stylesheet" href="https://fonts.googleapis.com/css2?family=Montserrat:wght@400;500;600;700&display=swap">
<style>
:root{
  --navy:#2b3a63;
  --red:#c0232b;
  --ink:#1c1c1c;
  --grey:#e8e8e8;
  --white:#ffffff;
  --field:#f2f2f2;
}
*{box-sizing:border-box;margin:0;padding:0}
html,body{width:1200px;height:2541px;overflow:hidden}
body{font-family:"Montserrat",sans-serif;color:var(--ink);background:var(--white);position:relative}
.abs{position:absolute}
.btn{position:absolute;display:flex;align-items:center;justify-content:center;font-size:15px;font-weight:500;border-radius:3px;text-transform:uppercase}
.btn-red{background:var(--red);color:var(--white)}
.btn-outline{border:1.5px solid #333;color:#222;background:rgba(255,255,255,.15)}

.site-header{position:absolute;top:0;left:0;width:1200px;height:86px;background:var(--white);z-index:3;box-shadow:0 1px 4px rgba(0,0,0,.08)}
.brand{position:absolute;left:112px;top:26px;display:flex;align-items:center;gap:10px;font-size:17px;font-weight:700;color:var(--navy)}
.brand-mark{width:30px;height:30px;background:var(--navy);border-radius:3px}
.main-nav{position:absolute;top:33px;left:491px;display:flex;gap:52px;font-size:14.5px;font-weight:500;color:#222}

.hero{position:absolute;top:86px;left:0;width:1200px;height:591px;background:linear-gradient(180deg,#d7dfe8 0%,#c9d3de 40%,#9aa6b3 60%,#7d8c72 85%,#6f7b64 100%)}
.hero-title{position:absolute;left:108px;top:112px;font-size:45px;line-height:52px;font-weight:400;letter-spacing:.5px;color:#111}
.hero-title strong{font-weight:700;color:var(--navy);display:block}
.hero-text{position:absolute;left:112px;top:224px;width:460px;font-size:15.5px;line-height:24px;color:#222}
.scroll-cue{position:absolute;left:581px;top:658px;width:38px;height:38px;border-radius:50%;background:var(--white);box-shadow:0 1px 5px rgba(0,0,0,.25);z-index:2;display:flex;align-items:center;justify-content:center}

.section-title{position:absolute;font-size:35px;line-height:42px;font-weight:400;color:#111;letter-spacing:.3px}
.section-title strong{display:block;font-weight:700;color:var(--navy)}
.body-text{position:absolute;font-size:14.6px;line-height:22.3px;color:#333}
.body-text p+p{margin-top:11px}

.about{position:absolute;top:677px;left:0;width:1200px;height:529px;background:var(--grey)}
.services{position:absolute;top:1206px;left:0;width:1200px;height:707px;background:var(--white)}
.plan{position:absolute;top:256px;width:316px}
.plan-tab{margin:0 5px;height:38px;background:var(--navy);color:var(--white);display:flex;align-items:center;justify-content:space-between;padding:0 9px 0 11px;font-size:14.5px;font-weight:500;border-radius:3px 3px 0 0}
.plan-tab .price{border-left:1px solid rgba(255,255,255,.7);padding-left:20px}
.plan.featured .plan-tab{background:var(--red)}
.arrow{position:absolute;top:1822px;width:34px;height:34px;border-radius:50%;display:flex;align-items:center;justify-content:center}

.proposal{position:absolute;top:1913px;left:0;width:1200px;height:571px;background:var(--grey)}
.field{position:absolute;height:35px;border:1px solid #9c9c9c;border-radius:3px;background:var(--field);font-size:13px;color:#444;padding:9px 12px}
.site-footer{position:absolute;top:2484px;left:0;width:1200px;height:57px;background:var(--navy);color:var(--white);font-size:14.5px}
</style>
</head>
<body>

<header class="site-header">
  <div class="brand"><span class="brand-mark"></span>Larkfield Ridge Management</div>
  <nav class="main-nav"><span>HOME</span><span>SERVICES</span><span>ABOUT</span><span>CONTACT US</span></nav>
  <span class="btn btn-red" style="left:955px;top:26px;width:134px;height:34px">Get a Quote</span>
</header>

<section class="hero" role="img" aria-label="Photo of a suburban street lined with new family homes under a soft sky">
  <h1 class="hero-title"><strong>PROPERTY MANAGEMENT</strong>DONE RIGHT.</h1>
  <p class="hero-text">Larkfield Ridge Management provides reliable, professional property management services that protect your investment and give you peace of mind.</p>
  <span class="btn btn-red" style="left:112px;top:319px;width:142px;height:35px">Our Services</span>
  <span class="btn btn-outline" style="left:266px;top:319px;width:143px;height:35px">Get a Quote</span>
</section>
<div class="scroll-cue">
  <svg width="14" height="20" viewBox="0 0 14 20"><rect x="1" y="1" width="12" height="18" rx="6" fill="none" stroke="#333" stroke-width="1.4"/><line x1="7" y1="4" x2="7" y2="8" stroke="#333" stroke-width="1.4"/></svg>
</div>

<section class="about">
  <h2 class="section-title" style="left:110px;top:98px"><strong>ABOUT OUR PROPERTY</strong>MANAGEMENT SOLUTIONS</h2>
  <div class="body-text" style="left:110px;top:201px;width:500px">
    <p>Our organization delivers comprehensive property management solutions that optimize asset performance and tenant satisfaction. By integrating advanced analytics with proven operational frameworks, our specialists ensure each property achieves sustained value appreciation.</p>
    <p>Drawing on decades of collective expertise, the team facilitates regulatory compliance, cost efficiency, and proactive maintenance.</p>
  </div>
  <span class="btn btn-red" style="left:110px;top:391px;width:128px;height:34px">Read More</span>
  <svg class="abs" style="left:671px;top:85px" width="420" height="360" viewBox="0 0 420 360" role="img" aria-label="Photo of a modern apartment building with balconies against a blue sky">
    <defs><linearGradient id="aboutFill" x1="0" y1="0" x2="0" y2="1"><stop offset="0" stop-color="#7fb2d6"/><stop offset=".6" stop-color="#8a7c73"/><stop offset="1" stop-color="#5a4c44"/></linearGradient></defs>
    <path d="M0 0H420V270Q420 280 410 285L220 356Q210 360 200 356L10 285Q0 280 0 270Z" fill="#6e8fae"/>
    <path d="M17 14H403V262Q403 270 395 274L218 340Q210 343 202 340L25 274Q17 270 17 262Z" fill="url(#aboutFill)" stroke="#ffffff" stroke-width="4"/>
  </svg>
</section>

<section class="services">
  <h2 class="section-title" style="left:112px;top:82px"><strong>STRATEGIC PROPERTY</strong>MANAGEMENT SOLUTIONS</h2>
  <p class="body-text" style="left:714px;top:81px;width:380px">Our analysis demonstrates that effective property oversight originates from meticulous operational planning, transparent communication channels, and data-driven performance metrics across every asset class.</p>

  <div class="plan" style="left:105px">
    <div class="plan-tab"><span>BASE SERVICE</span><span class="price">$99.00</span></div>
    <svg width="316" height="295" viewBox="0 0 316 295" role="img" aria-label="Photo of a brick family house"><defs><linearGradient id="p1" x1="0" y1="0" x2="0" y2="1"><stop offset="0" stop-color="#cfd4d8"/><stop offset=".5" stop-color="#a0614a"/><stop offset="1" stop-color="#6d6a45"/></linearGradient></defs><path d="M4 0H312V228Q312 238 302 243L168 290Q158 294 148 290L14 243Q4 238 4 228Z" fill="url(#p1)" stroke="#2b3a63" stroke-width="5"/></svg>
  </div>
  <div class="plan" style="left:444px">
    <div class="plan-tab"><span>INTERMEDIATE SERVICE</span><span class="price">$149.00</span></div>
    <svg width="316" height="295" viewBox="0 0 316 295" role="img" aria-label="Photo of a white modern townhouse with trees"><defs><linearGradient id="p2" x1="0" y1="0" x2="0" y2="1"><stop offset="0" stop-color="#3f8ee0"/><stop offset=".45" stop-color="#e7ecef"/><stop offset="1" stop-color="#55704a"/></linearGradient></defs><path d="M4 0H312V228Q312 238 302 243L168 290Q158 294 148 290L14 243Q4 238 4 228Z" fill="url(#p2)" stroke="#2b3a63" stroke-width="5"/></svg>
  </div>
  <div class="plan featured" style="left:783px">
    <div class="plan-tab"><span>ADVANCED SERVICE</span><span class="price">$199.00</span></div>
    <svg width="316" height="295" viewBox="0 0 316 295" role="img" aria-label="Photo of a white high-rise apartment block"><defs><linearGradient id="p3" x1="0" y1="0" x2="0" y2="1"><stop offset="0" stop-color="#c9d6e2"/><stop offset=".6" stop-color="#e4e4e2"/><stop offset="1" stop-color="#8c9078"/></linearGradient></defs><path d="M4 0H312V228Q312 238 302 243L168 290Q158 294 148 290L14 243Q4 238 4 228Z" fill="url(#p3)" stroke="#c0232b" stroke-width="5"/></svg>
  </div>
</section>
<span class="arrow" style="left:558px;background:var(--red)"><svg width="12" height="14" viewBox="0 0 12 14"><path d="M8 2L3 7L8 12" fill="none" stroke="#fff" stroke-width="2"/></svg></span>
<span class="arrow" style="left:607px;border:1.5px solid #222"><svg width="12" height="14" viewBox="0 0 12 14"><path d="M4 2L9 7L4 12" fill="none" stroke="#222" stroke-width="1.6"/></svg></span>

<section class="proposal">
  <h2 class="section-title" style="left:112px;top:80px;color:#111;font-weight:700"><strong>REQUEST A</strong>TAILORED PROPOSAL</h2>
  <p class="body-text" style="left:587px;top:124px;width:500px">Submit the form to initiate a consultative assessment and explore solutions aligned with your objectives.</p>
  <div class="abs" role="img" aria-label="Image of a small white model house" style="left:60px;top:205px;width:460px;height:270px;background:radial-gradient(ellipse at 60% 55%,#ffffff 0%,#d6d6d6 45%,rgba(232,232,232,0) 72%)"></div>
  <div class="field" style="left:587px;top:198px;width:244px">First Name</div>
  <div class="field" style="left:845px;top:198px;width:244px">Last Name</div>
  <div class="field" style="left:587px;top:252px;width:244px">Email</div>
  <div class="field" style="left:845px;top:252px;width:244px">Phone</div>
  <div class="field" style="left:587px;top:305px;width:502px;height:117px">Message</div>
  <span class="btn btn-red" style="left:588px;top:454px;width:106px;height:34px">Submit</span>
</section>

<footer class="site-footer">
  <span class="abs" style="left:112px;top:20px">© 2026 Larkfield Ridge Management LLC. All rights reserved.</span>
  <span class="abs" style="right:110px;top:20px;display:flex;align-items:center;gap:6px">
    <svg width="14" height="11" viewBox="0 0 14 11"><rect x="0" y="0" width="14" height="11" rx="1" fill="#fff"/><path d="M0.5 1L7 6L13.5 1" fill="none" stroke="#2b3a63" stroke-width="1.4"/></svg>
    info@larkfieldridgemanagement.com
  </span>
</footer>

</body>
</html>
```